Images and design ideas provided: Postcard size flier

2 sided postcard size flier to hand people on the street.

A FUN tax business needs a postcard size flier to hand people on the street. Not a typical serious, quiet, office so make the image fun!

Exact wording, logo and key images provided. You are free to add other images as you see fit (such as money).

Side 1: Use image of lady looking up (she should be looking at text provided).All spanish and english text provided. Logo in bottom right corner. Address at bottom of card.

Side 2: Image of lady holding money and pointing. Remove money and have her holding a sign/or some other creative way to have her looking at text. All spanish and english text provided. Logo in bottom right corner. Address at bottom of card.

Size: 4" x 6" horizontal or vertical is ok
Each side can be different and image/design does not have to be related.

Target Market(s)

Age 18-35

Industry/Entity Type

Accounting

Font styles to use
Sans Serif

Colors

Designer to choose colors to be used in the design.

Requirements
Must have
• Use text document provided. All text goes on both sides.
• Should be easy to read from a few feet away.
Nice to have
• Bright colors to attract attention of people walking by to grab flier/card. Images of money ok.
Should not have
• No images of calculators or typical accounting tax forms.

```html
<!DOCTYPE html>
<html lang="en">
<head>
<meta charset="utf-8">
<title>Refund Royale – Postcard Flier</title>
<link rel="stylesheet" href="https://fonts.googleapis.com/css2?family=Open+Sans:wght@700;800&family=Source+Sans+3:wght@400;600;700&display=swap">
<style>
  :root {
    --stage: #1b1b1b;
    --label: #d9d9d9;
    --red: #e8283f;
    --red-dark: #b81d31;
    --blue: #3474bb;
    --blue-dark: #285d98;
    --text-blue: #2f6db5;
    --ink: #1e1e1e;
    --white: #ffffff;
    --gold-1: #f6d77a;
    --gold-2: #c98f1c;
    --sky-1: #ffffff;
    --sky-2: #cfdff5;
  }
  * { margin: 0; padding: 0; box-sizing: border-box; }
  html, body { width: 1091px; height: 1200px; overflow: hidden; background: var(--stage); }
  body { position: relative; font-family: "Source Sans 3", sans-serif; }

  .side-label {
    position: absolute; left: 92px; color: var(--label);
    font-family: "Open Sans", sans-serif; font-weight: 800; font-size: 46px;
    letter-spacing: 2px; transform: translate(-50%, -50%) rotate(-90deg);
    white-space: nowrap;
  }
  .side-label--front { top: 340px; }
  .side-label--back { top: 862px; }

  .card {
    position: absolute; left: 226px; width: 727px; height: 485px; overflow: hidden;
    background: radial-gradient(ellipse at 70% 60%, var(--sky-1) 20%, var(--sky-2) 100%);
    box-shadow: 0 2px 6px rgba(0,0,0,.5);
  }
  .card--front { top: 96px; }
  .card--back { top: 624px; }
  .card__shapes { position: absolute; inset: 0; }

  .photo { position: absolute; }
  .card--front .photo {
    left: 10px; top: 178px; width: 330px; height: 307px;
    background: linear-gradient(180deg, #c8b06a 0%, #8a9a5e 45%, #7b8a55 75%, #a43a3a 100%);
    border-radius: 40% 40% 0 0 / 20% 20% 0 0;
  }
  .card--back .photo {
    left: 0; top: 0; width: 300px; height: 485px;
    background: linear-gradient(180deg, #d9b04a 0%, #c8463e 22%, #d8b8a0 40%, #7f8d57 70%, #8c7a60 100%);
    border-radius: 0 45% 0 0 / 0 20% 0 0;
  }

  .block { position: absolute; text-align: center; white-space: nowrap; }
  .headline {
    font-family: "Open Sans", sans-serif; font-weight: 800; color: var(--white);
    line-height: 1;
  }
  .amount {
    background: linear-gradient(180deg, var(--gold-1) 0%, var(--gold-2) 100%);
    -webkit-background-clip: text; background-clip: text; color: transparent;
  }
  .subline { font-weight: 400; color: var(--white); line-height: 1; }
  .spanish { font-family: "Open Sans", sans-serif; font-weight: 800; line-height: 1.18; }
  .spanish__note { color: var(--ink); line-height: 1.3; }
  .brand {
    display: flex; align-items: center; gap: 12px; justify-content: center;
    font-family: "Source Sans 3", sans-serif; font-weight: 700; color: var(--red);
    font-size: 30px; letter-spacing: 1px; text-transform: uppercase;
  }
  .brand__mark { width: 30px; height: 30px; border-radius: 50%; background: var(--text-blue); }
  .address { color: var(--ink); font-size: 17px; }
  .phone { font-family: "Open Sans", sans-serif; font-weight: 700; color: var(--ink); font-size: 38px; line-height: 1; }

  /* front */
  .card--front .headline { left: 0; width: 727px; top: 18px; font-size: 62px; padding-left: 2px; }
  .card--front .subline { left: 0; width: 736px; top: 84px; font-size: 38px; }
  .card--front .spanish { left: 354px; width: 340px; top: 178px; font-size: 40px; color: var(--text-blue); }
  .card--front .spanish .amount-es { color: var(--red); }
  .card--front .spanish__note { left: 354px; width: 340px; top: 274px; font-size: 20px; }
  .card--front .brand { left: 364px; width: 320px; top: 346px; }
  .card--front .address { left: 364px; width: 320px; top: 406px; }
  .card--front .phone { left: 364px; width: 320px; top: 428px; }

  /* back */
  .card--back .headline { left: 230px; width: 465px; top: 22px; font-size: 44px; }
  .card--back .subline { left: 230px; width: 450px; top: 70px; font-size: 34px; }
  .card--back .spanish { left: 330px; width: 365px; top: 166px; font-size: 45px; color: var(--red); line-height: 1.16; }
  .card--back .spanish .amount-es { color: var(--text-blue); }
  .card--back .spanish__note { left: 330px; width: 365px; top: 278px; font-size: 21px; line-height: 1.4; }
  .card--back .brand { left: 364px; width: 320px; top: 350px; }
  .card--back .address { left: 364px; width: 320px; top: 407px; }
  .card--back .phone { left: 364px; width: 320px; top: 430px; }
</style>
</head>
<body>
  <div class="side-label side-label--front">FRONT</div>
  <div class="side-label side-label--back">BACK</div>

  <section class="card card--front">
    <svg class="card__shapes" width="727" height="485" viewBox="0 0 727 485" aria-hidden="true">
      <path d="M0 272 C250 175 520 140 727 158 V166 C520 150 260 190 0 290 Z" fill="var(--red-dark)"/>
      <path d="M0 0 H727 V158 C520 140 250 175 0 272 Z" fill="var(--red)"/>
    </svg>
    <div class="photo" role="img" aria-label="Photo of a smiling woman in a king costume with crown hat, arms raised, looking up at the headline"></div>
    <div class="block headline">Get <span class="amount">$100</span> Cash Now!</div>
    <div class="block subline">with paid tax preparation</div>
    <div class="block spanish">Reciba <span class="amount-es">$100</span> en<br>efectivo ahora!</div>
    <div class="block spanish__note">con la preparacion pagada<br>de sus impuestos</div>
    <div class="block brand"><span class="brand__mark"></span>Refund Royale</div>
    <div class="block address">418 Harlow Ave. Bronx NY 10457</div>
    <div class="block phone">(718) 555-0148</div>
  </section>

  <section class="card card--back">
    <svg class="card__shapes" width="727" height="485" viewBox="0 0 727 485" aria-hidden="true">
      <path d="M0 178 C250 140 520 120 727 135 V146 C520 132 250 152 0 200 Z" fill="var(--blue-dark)"/>
      <path d="M0 0 H727 V135 C520 120 250 140 0 178 Z" fill="var(--blue)"/>
    </svg>
    <div class="photo" role="img" aria-label="Photo of a smiling woman in a king costume with crown hat, holding a fan of dollar bills toward the viewer"></div>
    <div class="block headline">Get <span class="amount">$100</span> Cash Now!</div>
    <div class="block subline">with paid tax preparation</div>
    <div class="block spanish">Reciba <span class="amount-es">$100</span> en<br>efectivo ahora!</div>
    <div class="block spanish__note">con la preparacion pagada<br>de sus impuestos</div>
    <div class="block brand"><span class="brand__mark"></span>Refund Royale</div>
    <div class="block address">418 Harlow Ave. Bronx NY 10457</div>
    <div class="block phone">(718) 555-0148</div>
  </section>
</body>
</html>
```